web page look and feel - B2B enterprise application

We have an enterprise application with 10 to 15 core pages and several supporting pages or popups. To start, we want the graphical design of the Users, Roles and Data Source pages and their supporting popups, wizards, etc. to be made beautiful. That is around 10 pages in total. There is a fair amount of redundancy among the pages. I have attached 5 screenshots. We very much want the pages to project a premium feel. That is absolutely essential. The color scheme is blue and sometimes yellow (only if it makes the page look better) plus black, gray and white. If the design of these screens goes well, we would expand the project to continue with other pages. The core of what we are looking for is graphic in nature but we are open to workflow suggestions if you have them. The Roles screen needs some improvements to the layout. I am looking for everything that includes icons, fonts, spacing, etc. I assume getting to the final design will take some back and forth with multiple revisions.

Target Market(s)

Large Enterprises

Number of Pages Required

5+ page

Requirements
Must have
• Premium feel

```html
<!DOCTYPE html>
<html lang="en">
<head>
<meta charset="utf-8">
<title>Users – Norvale Data</title>
<link href="https://fonts.googleapis.com/css2?family=Dosis:wght@400;500;600&family=Montserrat:wght@400;500&display=swap" rel="stylesheet">
<style>
:root{
  --brand-a:#27c0cc;
  --brand-b:#1a9ad8;
  --side:#173a55;
  --side-active:#234c6b;
  --side-text:#e8eef3;
  --accent:#0ea5d6;
  --accent-soft:#3fc2ef;
  --ok:#19c98a;
  --ink:#4a4f55;
  --ink-soft:#6b7177;
  --line:#d3d6d9;
  --band:#f3f3f3;
  --muted:#9aa0a6;
}
*{box-sizing:border-box;margin:0;padding:0}
html,body{width:1200px;height:786px;overflow:hidden;background:#fff}
body{position:relative;font-family:"Dosis",sans-serif;color:var(--ink)}
.brand{position:absolute;left:0;top:0;width:300px;height:80px;background:linear-gradient(100deg,var(--brand-a),var(--brand-b));display:flex;align-items:center;padding-left:44px;gap:10px}
.brand-dot{width:26px;height:26px;border-radius:50%;background:#fff}
.brand-name{font-family:"Dosis",sans-serif;font-weight:600;font-size:28px;color:#fff}
.sidebar{position:absolute;left:0;top:80px;width:300px;height:706px;background:var(--side);color:var(--side-text)}
.profile{position:absolute;left:40px;top:20px;display:flex;gap:10px;align-items:center}
.avatar{width:40px;height:40px;border-radius:50%;background:radial-gradient(circle at 50% 40%,#c79a7c,#6b4a3a);border:2px solid #fff}
.profile-name{font-family:"Montserrat",sans-serif;font-size:15px;font-weight:500;color:#fff;margin-bottom:3px}
.profile-mail{font-family:"Montserrat",sans-serif;font-size:12px;color:#b7c4cf}
.side-rule{position:absolute;left:20px;top:80px;width:260px;height:1px;background:#3a5a74}
.menu{position:absolute;left:20px;top:96px;width:280px;list-style:none}
.menu li{height:32px;display:flex;align-items:center;font-size:15px;padding-left:20px;gap:12px;position:relative}
.menu li.sub{padding-left:42px;gap:8px;font-size:14.5px}
.menu li.open{background:var(--side-active)}
.menu li.open::after{content:"";position:absolute;right:0;top:0;width:5px;height:32px;background:var(--accent)}
.menu .caret{position:absolute;right:34px;top:11px}
.menu svg{flex:none}
.clock{position:absolute;top:578px;left:30px;width:240px;display:flex;justify-content:space-between;font-size:15px;font-weight:600;color:#fff}
.clock span{display:flex;align-items:center;gap:8px}
.topbar{position:absolute;left:300px;top:0;width:900px;height:80px;border-bottom:1px solid #e6e6e6}
.topbar .burger{position:absolute;left:30px;top:31px}
.tools{position:absolute;left:490px;top:27px;display:flex;gap:23px}
.account{position:absolute;left:742px;top:28px;display:flex;align-items:center;gap:12px;font-size:17px;font-weight:500;color:#5a6066}
.page-head{position:absolute;left:357px;top:112px;display:flex;align-items:center;gap:18px}
.page-title{font-family:"Montserrat",sans-serif;font-size:31px;font-weight:400;color:#4a4f55}
.btn-add{background:var(--accent);color:#fff;font-weight:600;font-size:15px;padding:3px 16px;border-radius:2px;box-shadow:0 0 10px rgba(14,165,214,.5)}
.search{position:absolute;left:1087px;top:124px;display:flex;align-items:center;gap:14px;font-size:16px;color:#9aa0a6}
table{border-collapse:collapse;table-layout:fixed;position:absolute;left:330px;width:840px;font-size:15.5px}
td,th{border:1px solid var(--line);height:39px;text-align:center;font-weight:400;color:var(--ink)}
th{font-weight:500;font-size:16px}
.users-a{top:188px}
.users-b{top:511px}
.toggle{color:#a5abb0}
.actions{display:flex;justify-content:center;gap:10px}
.act{width:20px;height:20px;background:var(--accent);border-radius:2px;display:flex;align-items:center;justify-content:center}
.detail{position:absolute;left:330px;top:266px;width:840px;border-collapse:collapse}
.detail td{width:420px}
.detail .head td{background:var(--band)}
.perm{display:inline-flex;align-items:center;gap:6px;margin:0 8px}
.edit-bar{position:absolute;left:330px;top:461px;width:840px;height:39px;background:var(--accent);color:#fff;font-weight:600;font-size:16px;display:flex;align-items:center;justify-content:center}
.pager{position:absolute;left:677px;top:737px;display:flex;align-items:center;gap:5px;font-size:15px;color:#b0b5ba}
.pager .current{color:#666}
.pager .size{margin-left:16px;background:#8a8d90;color:#fff;font-weight:600;font-size:13px;padding:0 5px;height:17px;display:flex;align-items:center;gap:2px;border-radius:1px}
</style>
</head>
<body>
<header class="brand"><span class="brand-dot"></span><span class="brand-name">Norvale Data</span></header>

<nav class="sidebar">
  <div class="profile">
    <div class="avatar" role="img" aria-label="Profile photo of the signed-in user"></div>
    <div><div class="profile-name">Dana Whitlow</div><div class="profile-mail">dana.whitlow@example.com</div></div>
  </div>
  <div class="side-rule"></div>
  <ul class="menu">
    <li class="open"><svg width="16" height="16" viewBox="0 0 16 16"><circle cx="8" cy="5" r="3.5" fill="#29a9e1"/><path d="M1.5 16c0-4 3-6 6.5-6s6.5 2 6.5 6z" fill="#29a9e1"/></svg>User<svg class="caret" width="10" height="6" viewBox="0 0 10 6"><path d="M1 1l4 4 4-4" stroke="#cfd8df" fill="none" stroke-width="1.4"/></svg></li>
    <li class="sub"><svg width="18" height="18" viewBox="0 0 18 18" fill="none" stroke="#fff" stroke-width="1.2"><circle cx="9" cy="5.5" r="3.5"/><path d="M2.5 17c0-4 3-6 6.5-6s6.5 2 6.5 6z"/></svg>Roles</li>
    <li class="sub"><svg width="18" height="18" viewBox="0 0 18 18" fill="none" stroke="#fff" stroke-width="1.2"><path d="M4 13V8a5 5 0 0110 0v5l2 2H2z"/><path d="M7 16a2 2 0 004 0"/></svg>Notification Groups</li>
    <li class="open"><svg width="18" height="16" viewBox="0 0 18 16" fill="#29a9e1"><rect x="0" y="0" width="18" height="4"/><rect x="0" y="6" width="18" height="4"/><rect x="0" y="12" width="18" height="4"/></svg>Data Source<svg class="caret" width="10" height="6" viewBox="0 0 10 6"><path d="M1 1l4 4 4-4" stroke="#cfd8df" fill="none" stroke-width="1.4"/></svg></li>
    <li class="sub"><svg width="18" height="18" viewBox="0 0 18 18" fill="none" stroke="#fff" stroke-width="1.2"><path d="M6 2h10v14H6"/><path d="M1 9h10M8 6l3 3-3 3"/></svg>Data Object Relationship</li>
    <li><svg width="18" height="18" viewBox="0 0 18 18" fill="#fff"><rect x="0" y="0" width="8" height="18"/><rect x="10" y="0" width="8" height="8"/><rect x="10" y="10" width="8" height="8"/></svg>Data Sets</li>
    <li><svg width="18" height="18" viewBox="0 0 18 18" fill="#fff"><rect x="0" y="0" width="7" height="18"/><rect x="9" y="1" width="9" height="2"/><rect x="9" y="6" width="9" height="2"/><rect x="9" y="11" width="9" height="2"/><rect x="9" y="16" width="9" height="2"/></svg>Rule Sets</li>
    <li><svg width="18" height="18" viewBox="0 0 18 18" fill="none" stroke="#fff" stroke-width="1.5"><circle cx="9" cy="9" r="8"/><path d="M9 4v5l3 2"/></svg>Schedule</li>
    <li class="open"><svg width="18" height="18" viewBox="0 0 18 18" fill="none" stroke="#29a9e1" stroke-width="1.6"><path d="M2 8a7 7 0 0113-2M16 10a7 7 0 01-13 2"/><path d="M15 2v4h-4M3 16v-4h4"/></svg>Metadata Import/Export<svg class="caret" width="10" height="6" viewBox="0 0 10 6"><path d="M1 1l4 4 4-4" stroke="#cfd8df" fill="none" stroke-width="1.4"/></svg></li>
    <li class="sub"><svg width="14" height="18" viewBox="0 0 14 18" fill="none" stroke="#fff" stroke-width="1.4"><path d="M7 1v15M2 11l5 5 5-5"/></svg>Import</li>
    <li class="sub"><svg width="14" height="18" viewBox="0 0 14 18" fill="none" stroke="#fff" stroke-width="1.4"><path d="M7 17V2M2 7l5-5 5 5"/></svg>Export</li>
  </ul>
  <div class="clock">
    <span><svg width="24" height="26" viewBox="0 0 24 26" fill="none" stroke="#fff" stroke-width="2"><rect x="1" y="4" width="22" height="21" rx="2"/><path d="M1 10h22M6 1v5M18 1v5"/><text x="12" y="22" font-size="11" font-family="Dosis,sans-serif" font-weight="600" fill="#fff" stroke="none" text-anchor="middle">5</text></svg>July 05</span>
    <span><svg width="24" height="24" viewBox="0 0 24 24" fill="none" stroke="#fff" stroke-width="2"><circle cx="12" cy="12" r="11"/><path d="M12 5v8h-4"/></svg>18:36</span>
  </div>
</nav>

<div class="topbar">
  <svg class="burger" width="18" height="16" viewBox="0 0 18 16" fill="#666"><rect y="0" width="18" height="3"/><rect y="6.5" width="18" height="3"/><rect y="13" width="18" height="3"/></svg>
  <div class="tools">
    <svg width="28" height="26" viewBox="0 0 28 26" fill="none" stroke="#666" stroke-width="2.2"><path d="M3 20a11 11 0 0122 0"/><path d="M14 19l5-7"/></svg>
    <svg width="27" height="26" viewBox="0 0 27 26" fill="none" stroke="#666" stroke-width="2.4"><path d="M3 24L18 9"/><path d="M21 2v3M24 6h-3M23 11l-1-1M15 3l1 1" stroke-width="1.4"/></svg>
    <svg width="27" height="27" viewBox="0 0 27 27"><circle cx="13" cy="13" r="12" fill="#1a9ad8"/><text x="13" y="19" font-size="17" font-family="Dosis,sans-serif" font-weight="600" fill="#fff" text-anchor="middle">?</text></svg>
    <svg width="27" height="27" viewBox="0 0 27 27" fill="#777"><circle cx="9" cy="10" r="7"/><circle cx="19" cy="19" r="6"/><circle cx="9" cy="10" r="2.5" fill="#fff"/><circle cx="19" cy="19" r="2" fill="#fff"/></svg>
  </div>
  <div class="account">
    <svg width="20" height="26" viewBox="0 0 20 26" fill="#777"><circle cx="10" cy="6" r="5.5"/><path d="M0 26v-6c0-4 4-7 10-7s10 3 10 7v6z"/></svg>
    Dana Whitlow
    <svg width="12" height="7" viewBox="0 0 12 7"><path d="M1 1l5 5 5-5" stroke="#777" fill="none" stroke-width="1.4"/></svg>
  </div>
</div>

<div class="page-head"><h1 class="page-title">Users</h1><span class="btn-add">Add</span></div>
<div class="search"><svg width="22" height="22" viewBox="0 0 22 22" fill="none" stroke="#9aa0a6" stroke-width="1.6"><circle cx="9" cy="9" r="8"/><path d="M15 15l6 6"/></svg>Search</div>

<table class="users-a">
  <colgroup><col style="width:40px"><col style="width:137px"><col style="width:137px"><col style="width:137px"><col style="width:137px"><col style="width:137px"><col style="width:115px"></colgroup>
  <tr><th></th><th>First Name</th><th>Last Name</th><th>Username</th><th>Email</th><th>Status</th><th>Edit</th></tr>
  <tr><td class="toggle"><svg width="7" height="11" viewBox="0 0 7 11"><path d="M1 1l5 4.5L1 10" stroke="#a5abb0" fill="none" stroke-width="1.4"/></svg></td><td>Test</td><td>Test</td><td>test.1</td><td>test@demo.net</td><td>Active</td><td><div class="actions">
    <span class="act"><svg width="12" height="12" viewBox="0 0 12 12" fill="none" stroke="#fff" stroke-width="1.3"><path d="M2 10l1-3 6-6 2 2-6 6z"/><path d="M1 11.5h10"/></svg></span>
    <span class="act"><svg width="12" height="12" viewBox="0 0 12 12" fill="none" stroke="#fff" stroke-width="1.3"><rect x="4" y="4" width="7" height="7"/><path d="M1 8V1h7"/></svg></span>
    <span class="act"><svg width="12" height="12" viewBox="0 0 12 12" fill="none" stroke="#fff" stroke-width="1.3"><path d="M1 3h10M4 3V1h4v2M2.5 3l1 8h5l1-8M5 5v4M7 5v4"/></svg></span>
  </div></td></tr>
</table>

<table class="detail">
  <tr class="head"><td>Object</td><td>Permissions</td></tr>
  <tr><td>System Settings</td><td><span class="perm"><svg width="20" height="20" viewBox="0 0 20 20"><circle cx="10" cy="10" r="10" fill="#19c98a"/><path d="M5 10l3.5 3.5L15 7" stroke="#fff" stroke-width="2.4" fill="none"/></svg>Read</span><span class="perm"><svg width="20" height="20" viewBox="0 0 20 20"><circle cx="10" cy="10" r="10" fill="#19c98a"/><path d="M5 10l3.5 3.5L15 7" stroke="#fff" stroke-width="2.4" fill="none"/></svg>Write</span></td></tr>
  <tr><td>Users</td><td><span class="perm"><svg width="20" height="20" viewBox="0 0 20 20"><circle cx="10" cy="10" r="10" fill="#19c98a"/><path d="M5 10l3.5 3.5L15 7" stroke="#fff" stroke-width="2.4" fill="none"/></svg>Read</span><span class="perm"><svg width="20" height="20" viewBox="0 0 20 20"><circle cx="10" cy="10" r="10" fill="#19c98a"/><path d="M5 10l3.5 3.5L15 7" stroke="#fff" stroke-width="2.4" fill="none"/></svg>Write</span></td></tr>
  <tr class="head"><td>Data Source</td><td>Role</td></tr>
  <tr><td>All Data Sources</td><td>All Administrator</td></tr>
</table>
<div class="edit-bar">Edit</div>

<table class="users-b">
  <colgroup><col style="width:40px"><col style="width:137px"><col style="width:137px"><col style="width:137px"><col style="width:137px"><col style="width:137px"><col style="width:115px"></colgroup>
  <tr><td><svg width="11" height="7" viewBox="0 0 11 7"><path d="M1 1l4.5 4.5L10 1" stroke="#a5abb0" fill="none" stroke-width="1.4"/></svg></td><td>Test</td><td>Test</td><td>test.1</td><td>test@demo.net</td><td>Active</td><td><div class="actions"><span class="act"><svg width="12" height="12" viewBox="0 0 12 12" fill="none" stroke="#fff" stroke-width="1.3"><path d="M2 10l1-3 6-6 2 2-6 6z"/><path d="M1 11.5h10"/></svg></span><span class="act"><svg width="12" height="12" viewBox="0 0 12 12" fill="none" stroke="#fff" stroke-width="1.3"><rect x="4" y="4" width="7" height="7"/><path d="M1 8V1h7"/></svg></span><span class="act"><svg width="12" height="12" viewBox="0 0 12 12" fill="none" stroke="#fff" stroke-width="1.3"><path d="M1 3h10M4 3V1h4v2M2.5 3l1 8h5l1-8M5 5v4M7 5v4"/></svg></span></div></td></tr>
  <tr><td><svg width="11" height="7" viewBox="0 0 11 7"><path d="M1 1l4.5 4.5L10 1" stroke="#a5abb0" fill="none" stroke-width="1.4"/></svg></td><td>Test</td><td>Test</td><td>test.1</td><td>test@demo.net</td><td>Active</td><td><div class="actions"><span class="act"><svg width="12" height="12" viewBox="0 0 12 12" fill="none" stroke="#fff" stroke-width="1.3"><path d="M2 10l1-3 6-6 2 2-6 6z"/><path d="M1 11.5h10"/></svg></span><span class="act"><svg width="12" height="12" viewBox="0 0 12 12" fill="none" stroke="#fff" stroke-width="1.3"><rect x="4" y="4" width="7" height="7"/><path d="M1 8V1h7"/></svg></span><span class="act"><svg width="12" height="12" viewBox="0 0 12 12" fill="none" stroke="#fff" stroke-width="1.3"><path d="M1 3h10M4 3V1h4v2M2.5 3l1 8h5l1-8M5 5v4M7 5v4"/></svg></span></div></td></tr>
  <tr><td><svg width="11" height="7" viewBox="0 0 11 7"><path d="M1 1l4.5 4.5L10 1" stroke="#a5abb0" fill="none" stroke-width="1.4"/></svg></td><td>Test</td><td>Test</td><td>test.1</td><td>test@demo.net</td><td>Active</td><td><div class="actions"><span class="act"><svg width="12" height="12" viewBox="0 0 12 12" fill="none" stroke="#fff" stroke-width="1.3"><path d="M2 10l1-3 6-6 2 2-6 6z"/><path d="M1 11.5h10"/></svg></span><span class="act"><svg width="12" height="12" viewBox="0 0 12 12" fill="none" stroke="#fff" stroke-width="1.3"><rect x="4" y="4" width="7" height="7"/><path d="M1 8V1h7"/></svg></span><span class="act"><svg width="12" height="12" viewBox="0 0 12 12" fill="none" stroke="#fff" stroke-width="1.3"><path d="M1 3h10M4 3V1h4v2M2.5 3l1 8h5l1-8M5 5v4M7 5v4"/></svg></span></div></td></tr>
  <tr><td><svg width="11" height="7" viewBox="0 0 11 7"><path d="M1 1l4.5 4.5L10 1" stroke="#a5abb0" fill="none" stroke-width="1.4"/></svg></td><td>Test</td><td>Test</td><td>test.1</td><td>test@demo.net</td><td>Active</td><td><div class="actions"><span class="act"><svg width="12" height="12" viewBox="0 0 12 12" fill="none" stroke="#fff" stroke-width="1.3"><path d="M2 10l1-3 6-6 2 2-6 6z"/><path d="M1 11.5h10"/></svg></span><span class="act"><svg width="12" height="12" viewBox="0 0 12 12" fill="none" stroke="#fff" stroke-width="1.3"><rect x="4" y="4" width="7" height="7"/><path d="M1 8V1h7"/></svg></span><span class="act"><svg width="12" height="12" viewBox="0 0 12 12" fill="none" stroke="#fff" stroke-width="1.3"><path d="M1 3h10M4 3V1h4v2M2.5 3l1 8h5l1-8M5 5v4M7 5v4"/></svg></span></div></td></tr>
  <tr><td><svg width="11" height="7" viewBox="0 0 11 7"><path d="M1 1l4.5 4.5L10 1" stroke="#a5abb0" fill="none" stroke-width="1.4"/></svg></td><td>Test</td><td>Test</td><td>test.1</td><td>test@demo.net</td><td>Active</td><td><div class="actions"><span class="act"><svg width="12" height="12" viewBox="0 0 12 12" fill="none" stroke="#fff" stroke-width="1.3"><path d="M2 10l1-3 6-6 2 2-6 6z"/><path d="M1 11.5h10"/></svg></span><span class="act"><svg width="12" height="12" viewBox="0 0 12 12" fill="none" stroke="#fff" stroke-width="1.3"><rect x="4" y="4" width="7" height="7"/><path d="M1 8V1h7"/></svg></span><span class="act"><svg width="12" height="12" viewBox="0 0 12 12" fill="none" stroke="#fff" stroke-width="1.3"><path d="M1 3h10M4 3V1h4v2M2.5 3l1 8h5l1-8M5 5v4M7 5v4"/></svg></span></div></td></tr>
</table>

<div class="pager">
  <svg width="7" height="11" viewBox="0 0 7 11"><path d="M6 1L1.5 5.5 6 10" stroke="#666" fill="none" stroke-width="1.6"/></svg>
  <span class="current">1</span><span>2</span><span>3</span><span>4</span>
  <svg width="7" height="11" viewBox="0 0 7 11"><path d="M1 1l4.5 4.5L1 10" stroke="#666" fill="none" stroke-width="1.6"/></svg>
  <span class="size">20<svg width="7" height="5" viewBox="0 0 7 5"><path d="M1 1l2.5 2.5L6 1" stroke="#fff" fill="none" stroke-width="1.2"/></svg></span>
</div>
</body>
</html>
```